Alterations to existing business card

Here is my current logo and I want the "cafe and bar" taken off with just the words Lumo and our slogan "Savour the moment" on the card, Plus the logo.
Our Current Business Card is currently 5.5cm by 5.5cm and would like it to remain like this thanks.
The loyalty card can be 10 squares with the logo specifying the 10th coffee free. I would like the cheapest option please.
Also on our business card would like the Facebook logo and instagram Logo with TAZALUMO27 as link to our photos on instagram.

Keep Colour schemes the same please.

On the business cards

Dale Brinton Director
0427916038
dale27lumo@mailvista.test

Paula Ferrisi Principal
0428571963
paulumo@mailvista.test

Thanks Dale

Industry/Entity Type

Business

```html
<!DOCTYPE html>
<html lang="en">
<head>
<meta charset="utf-8">
<title>Lumo business and loyalty cards</title>
<link rel="stylesheet" href="https://fonts.googleapis.com/css2?family=Open+Sans:wght@300;400;600;700&display=swap">
<style>
  :root {
    --gold-light: #f3c95f;
    --gold-deep: #e6ae3c;
    --gold-text: #e8b443;
    --ink: #1d1d1d;
    --paper: #ffffff;
    --backdrop: #ece8e3;
  }
  * { box-sizing: border-box; margin: 0; padding: 0; }
  html, body { width: 1200px; height: 900px; overflow: hidden; }
  body {
    background: var(--backdrop);
    font-family: "Open Sans", Arial, sans-serif;
    color: var(--ink);
    position: relative;
  }
  .card {
    position: absolute;
    background: var(--paper);
    overflow: hidden;
    box-shadow: 0 6px 18px rgba(0,0,0,0.12);
  }
  .card-diagonal { position: absolute; inset: 0; width: 100%; height: 100%; }

  /* Contact card */
  .contact-card { left: 200px; top: 33px; width: 343px; height: 345px; }
  .person { position: absolute; }
  .person-principal { left: 30px; top: 18px; }
  .person-director { right: 26px; top: 205px; text-align: right; }
  .person-name { font-weight: 600; font-size: 19px; line-height: 1.3; }
  .person-principal .person-name { color: var(--gold-text); }
  .person-director .person-name { font-size: 21px; font-weight: 700; }
  .person-role { font-size: 15px; margin-top: 2px; }
  .contact-list { list-style: none; margin-top: 14px; font-size: 15px; }
  .person-director .contact-list { margin-top: 18px; }
  .contact-list li { display: flex; align-items: center; gap: 5px; line-height: 22px; }
  .person-director .contact-list li { justify-content: flex-end; }
  .contact-icon { width: 12px; height: 12px; flex: none; }
  .person-principal .contact-icon { fill: var(--gold-text); }
  .person-director .contact-icon { fill: var(--ink); }
  .envelope-fold { fill: none; stroke: var(--paper); stroke-width: 2; }
  .person-director .envelope-fold { stroke: var(--gold-light); }

  /* Loyalty card */
  .loyalty-card { left: 638px; top: 473px; width: 332px; height: 332px; }
  .brand { position: absolute; left: 30px; top: 24px; width: 120px; }
  .brand-mark {
    width: 84px; height: 84px; border-radius: 50%;
    border: 3px solid var(--gold-deep); margin-left: 6px;
  }
  .brand-name {
    margin-top: 16px; font-size: 30px; font-weight: 300;
    letter-spacing: 2px; color: var(--ink); line-height: 1;
  }
  .brand-slogan {
    font-size: 8px; font-weight: 600; letter-spacing: 0.4px;
    color: var(--gold-text); margin-top: 3px; text-transform: uppercase;
  }
  .stamp-grid { position: absolute; inset: 0; width: 100%; height: 100%; }
  .stamp { fill: var(--paper); }
  .stamp-label {
    fill: var(--gold-text); font-family: "Open Sans", Arial, sans-serif;
    font-weight: 700; font-size: 19px; text-anchor: middle; dominant-baseline: central;
  }
  .stamp-label-free { font-size: 12px; }
  .social-dot { fill: var(--ink); stroke: var(--paper); stroke-width: 2; }
</style>
</head>
<body>

<section class="card contact-card" aria-label="Lumo business card">
  <svg class="card-diagonal" viewBox="0 0 343 345" aria-hidden="true">
    <defs>
      <linearGradient id="goldFillA" x1="1" y1="0" x2="0" y2="1">
        <stop offset="0" stop-color="#f3c95f"/>
        <stop offset="1" stop-color="#e6ae3c"/>
      </linearGradient>
    </defs>
    <polygon points="343,0 343,345 0,345" fill="url(#goldFillA)"/>
  </svg>

  <div class="person person-principal">
    <p class="person-name">Paula Ferrisi</p>
    <p class="person-role">Principal</p>
    <ul class="contact-list">
      <li><svg class="contact-icon" viewBox="0 0 24 24"><path d="M6.6 10.8a15 15 0 0 0 6.6 6.6l2.2-2.2a1 1 0 0 1 1-.25 11.4 11.4 0 0 0 3.6.57 1 1 0 0 1 1 1V20a1 1 0 0 1-1 1A17 17 0 0 1 3 4a1 1 0 0 1 1-1h3.5a1 1 0 0 1 1 1c0 1.25.2 2.45.57 3.57a1 1 0 0 1-.25 1z"/></svg>0428571963</li>
      <li><svg class="contact-icon" viewBox="0 0 24 24"><path d="M2 5h20v14H2z"/><path class="envelope-fold" d="M2 6l10 7 10-7"/></svg>paulumo@mailvista.test</li>
    </ul>
  </div>

  <div class="person person-director">
    <p class="person-name">Dale Brinton</p>
    <p class="person-role">Director</p>
    <ul class="contact-list">
      <li>0427916038<svg class="contact-icon" viewBox="0 0 24 24"><path d="M6.6 10.8a15 15 0 0 0 6.6 6.6l2.2-2.2a1 1 0 0 1 1-.25 11.4 11.4 0 0 0 3.6.57 1 1 0 0 1 1 1V20a1 1 0 0 1-1 1A17 17 0 0 1 3 4a1 1 0 0 1 1-1h3.5a1 1 0 0 1 1 1c0 1.25.2 2.45.57 3.57a1 1 0 0 1-.25 1z"/></svg></li>
      <li>dale27lumo@mailvista.test<svg class="contact-icon" viewBox="0 0 24 24"><path d="M2 5h20v14H2z"/><path class="envelope-fold" d="M2 6l10 7 10-7"/></svg></li>
    </ul>
  </div>
</section>

<section class="card loyalty-card" aria-label="Lumo loyalty card">
  <svg class="card-diagonal" viewBox="0 0 332 332" aria-hidden="true">
    <defs>
      <linearGradient id="goldFillB" x1="1" y1="0" x2="0" y2="1">
        <stop offset="0" stop-color="#f3c95f"/>
        <stop offset="1" stop-color="#e6ae3c"/>
      </linearGradient>
    </defs>
    <polygon points="332,0 332,332 0,332" fill="url(#goldFillB)"/>
  </svg>

  <div class="brand">
    <div class="brand-mark" aria-hidden="true"></div>
    <p class="brand-name">LUMO</p>
    <p class="brand-slogan">Savour the moment</p>
  </div>

  <svg class="stamp-grid" viewBox="0 0 332 332" aria-label="Ten stamp loyalty grid, tenth coffee free">
    <g>
      <circle class="stamp" cx="89" cy="245" r="20"/><text class="stamp-label" x="89" y="245" transform="rotate(-30 89 245)">1</text>
      <circle class="stamp" cx="125" cy="207" r="20"/><text class="stamp-label" x="125" y="207" transform="rotate(-30 125 207)">2</text>
      <circle class="stamp" cx="162" cy="163" r="20"/><text class="stamp-label" x="162" y="163" transform="rotate(-30 162 163)">3</text>
      <circle class="stamp" cx="200" cy="121" r="20"/><text class="stamp-label" x="200" y="121" transform="rotate(-30 200 121)">4</text>
      <circle class="stamp" cx="239" cy="76" r="20"/><text class="stamp-label" x="239" y="76" transform="rotate(-30 239 76)">5</text>
      <circle class="stamp" cx="126" cy="277" r="20"/><text class="stamp-label" x="126" y="277" transform="rotate(-30 126 277)">6</text>
      <circle class="stamp" cx="160" cy="237" r="20"/><text class="stamp-label" x="160" y="237" transform="rotate(-30 160 237)">7</text>
      <circle class="stamp" cx="198" cy="195" r="20"/><text class="stamp-label" x="198" y="195" transform="rotate(-30 198 195)">8</text>
      <circle class="stamp" cx="236" cy="155" r="20"/><text class="stamp-label" x="236" y="155" transform="rotate(-30 236 155)">9</text>
      <circle class="stamp" cx="275" cy="112" r="20"/><text class="stamp-label stamp-label-free" x="275" y="112" transform="rotate(-45 275 112)">Free</text>
    </g>
    <circle class="social-dot" cx="217" cy="255" r="16"/>
    <circle class="social-dot" cx="255" cy="222" r="16"/>
  </svg>
</section>

</body>
</html>
```